Local Flower Farm Needs Business Card Design

I need business cards designed for a flower farm based in Eudora, Kansas.
Business Info:
We are a local cut flower farm located in Eudora, Kansas, founded by Corinne Haldwick. What started as a passion for agriculture and search for more joy in daily life has blossomed into a small business dedicated to providing the community with beautiful, fresh, and sustainable flowers. We specialize in local, seasonal blooms, ensuring that every petal reflects the care and dedication we pour into our craft. Our mission is to deliver the highest quality flowers directly to our customers through local farmers markets and to florists who share our commitment to sustainability. Join us in celebrating the beauty of nature, one bloom at a time!
Contact Details:
Corinne Haldwick
Owner
Phone 913-555-0147
Facebook: Rosalind Thorpe Gardens
Instagram: @RosalindThorpeGardens
Website: RosalindThorpeGardens.example
Target Market(s)
Wholesale to Florists and Direct to Consumer via Farmers Market
Industry/Entity Type
Florist, Farm
Contact Information for Business Card
Name, Contact Info, Logo
Look and feel
Each slider illustrates characteristics of the customer's brand and the style your logo design should communicate.

```html
<!DOCTYPE html>
<html lang="en">
<head>
<meta charset="utf-8">
<title>Rosalind Thorpe Gardens – Business Card</title>
<link href="https://fonts.googleapis.com/css2?family=Libre+Baskerville:wght@400;700&family=Figtree:wght@400;500&display=swap" rel="stylesheet">
<style>
  :root {
    --backdrop: #9d9d9d;
    --ink: #0b2830;
    --paper: #ffffff;
    --paper-text: #1a1a1a;
    --reverse-text: #f4f6f6;
  }
  * { box-sizing: border-box; margin: 0; padding: 0; }
  html, body {
    width: 1093px; height: 1200px; overflow: hidden;
    background: var(--backdrop);
  }
  .canvas { position: relative; width: 1093px; height: 1200px; }

  .card {
    position: absolute; left: 265px; width: 580px; height: 356px;
    border-radius: 24px; overflow: hidden;
  }
  .card--front { top: 227px; background: var(--paper); }
  .card--back { top: 621px; background: var(--ink); }

  .name-block { position: absolute; left: 0; top: 43px; }
  .name-block__bar {
    position: absolute; left: 0; top: 0; width: 12px; height: 35px;
    background: var(--ink);
  }
  .name-block__name {
    position: absolute; left: 22px; top: -3px; white-space: nowrap;
    font: 400 21px/1 "Libre Baskerville", serif; color: var(--ink);
    letter-spacing: 0.3px;
  }
  .name-block__title {
    position: absolute; left: 22px; top: 20px;
    font: 400 16px/1 "Figtree", sans-serif; color: var(--paper-text);
  }

  .contacts { position: absolute; left: 22px; top: 226px; list-style: none; }
  .contacts li {
    display: flex; align-items: center; gap: 5px; height: 26.3px;
    font: 400 16.5px/1 "Figtree", sans-serif; color: var(--paper-text);
    white-space: nowrap;
  }
  .contacts svg { width: 22px; height: 22px; flex: none; }

  .wordmark {
    position: absolute; left: 300px; top: 60px; width: 260px;
    font: 700 42px/1.15 "Libre Baskerville", serif; color: var(--ink);
    text-align: right;
  }

  .seal {
    position: absolute; left: 192px; top: 64px; width: 196px; height: 196px;
    border: 1.5px solid var(--reverse-text); border-radius: 50%;
    display: flex; align-items: center; justify-content: center;
    text-align: center;
    font: 400 20px/1.3 "Libre Baskerville", serif; color: var(--reverse-text);
    letter-spacing: 1px;
  }
  .back-url {
    position: absolute; left: 0; right: 0; top: 301px; text-align: center;
    font: 400 17px/1 "Figtree", sans-serif; color: var(--reverse-text);
    letter-spacing: 1px;
  }
</style>
</head>
<body>
<main class="canvas">
  <section class="card card--front">
    <div class="name-block">
      <span class="name-block__bar"></span>
      <h1 class="name-block__name">CORINNE HALDWICK</h1>
      <p class="name-block__title">Owner</p>
    </div>

    <ul class="contacts">
      <li>
        <svg viewBox="0 0 22 22" aria-hidden="true"><circle cx="11" cy="11" r="10" fill="none" stroke="#1a1a1a" stroke-width="1"/><path d="M7.5 6.5l2 0 1 2.5-1.3 1c.6 1.3 1.5 2.2 2.8 2.8l1-1.3 2.5 1v2c-4.6.3-8.3-3.4-8-8z" fill="#1a1a1a"/></svg>
        913-555-0147
      </li>
      <li>
        <svg viewBox="0 0 22 22" aria-hidden="true"><circle cx="11" cy="11" r="10" fill="none" stroke="#1a1a1a" stroke-width="1"/></svg>
        Rosalind Thorpe Gardens
      </li>
      <li>
        <svg viewBox="0 0 22 22" aria-hidden="true"><circle cx="11" cy="11" r="10" fill="none" stroke="#1a1a1a" stroke-width="1"/></svg>
        @RosalindThorpeGardens
      </li>
      <li>
        <svg viewBox="0 0 22 22" aria-hidden="true"><circle cx="11" cy="11" r="10" fill="none" stroke="#1a1a1a" stroke-width="1"/><g fill="none" stroke="#1a1a1a" stroke-width="1"><circle cx="11" cy="11" r="5.5"/><ellipse cx="11" cy="11" rx="2.4" ry="5.5"/><path d="M5.5 11h11M6.3 8.3h9.4M6.3 13.7h9.4"/></g></svg>
        RosalindThorpeGardens.example
      </li>
    </ul>

    <p class="wordmark">Rosalind<br>Thorpe<br>Gardens</p>
  </section>

  <section class="card card--back">
    <div class="seal">Rosalind<br>Thorpe<br>Gardens</div>
    <p class="back-url">RosalindThorpeGardens.example</p>
  </section>
</main>
</body>
</html>
```